K7 Electrical Services Ltd Web design

I require a web site for my new electrical contracting company. We are customer service orientated. Offering high value electrical installations, design and maintenance. Focused on custom residential and commercial upgrading. Lighting design and application are paramount in our company's services. Industry leading product use and integration are always on the forefront with our customer client services. As well as energy efficiency.

Target Market(s)

Homebuilders, General Contractors, Property management companies, clients, individuals,

Industry/Entity Type

Electric Company

Coding

Coded - Design and coding required

Number of Pages Required

3 page

Requirements
Must have
• Classic, modern, edgy but not trendy . Appeals to the masse.
• 3 page
• home page
• about page
• gallery page
• ability to contact from the webiste
Nice to have
• open to all types of designs that are relative to the construction industry.
• Black, Grey, metallic ice blue and deep purple colours from the logo.
Should not have
• anything cheesy with cartoon light bulb images.

```html
<!DOCTYPE html>
<html lang="en">
<head>
<meta charset="utf-8">
<title>K7 Electrical Services Ltd</title>
<link href="https://fonts.googleapis.com/css2?family=Lato:ital,wght@0,400;0,700;0,900;1,400&display=swap" rel="stylesheet">
<style>
:root{
  --purple:#5c2a8a;
  --ink:#1d1d1d;
  --text:#555;
  --grey-bg:#efefef;
  --footer:#2d2d2d;
  --footer-text:#cfcfcf;
  --white:#fff;
  --star:#f5b400;
  --orange-a:#ffb300;
  --orange-b:#ff8a00;
  --link-purple:#9b6cc9;
}
*{margin:0;padding:0;box-sizing:border-box}
html,body{width:1200px;height:3175px;overflow:hidden}
body{font-family:'Lato',Arial,sans-serif;color:var(--ink);background:var(--white);position:relative}
section,header,footer{position:absolute;left:0;width:1200px}
.abs{position:absolute}
.photo{position:absolute}

/* header */
.site-header{top:0;height:155px;background:var(--white)}
.brand{left:74px;top:58px;display:flex;align-items:center;gap:12px}
.brand-mark{width:22px;height:22px;background:#6d6d6d}
.brand-name{font-size:24px;font-weight:700;color:#4a4a4a;line-height:1;white-space:nowrap}
.top-contact{right:74px;top:34px;display:flex;gap:22px;font-size:15px;font-weight:700;align-items:center}
.top-contact span{display:flex;align-items:center;gap:10px}
.top-contact .sep{width:1px;height:16px;background:var(--purple)}
.main-nav{right:74px;top:98px;display:flex;gap:34px;font-size:14px;font-weight:700;text-transform:uppercase}
.main-nav a{color:var(--ink);text-decoration:none;padding-bottom:8px}
.main-nav a.active{color:var(--purple);border-bottom:3px solid var(--purple)}

/* hero */
.hero{top:155px;height:505px;background:#ececec}
.hero .photo{left:360px;top:0;width:840px;height:505px;background:linear-gradient(100deg,#e8e8ea 0%,#c9ced8 30%,#7f8c9e 65%,#4c5566 100%)}
.hero-title{left:74px;top:118px;font-size:56px;font-weight:900;color:var(--purple);line-height:1.02}
.hero-sub{left:74px;top:240px;font-size:22px;font-weight:700}
.btn-outline{left:74px;top:295px;width:184px;height:50px;border:2px solid var(--ink);border-radius:25px;display:flex;align-items:center;justify-content:center;font-size:14px;font-weight:900;color:var(--purple)}
.dots{left:74px;top:450px;display:flex;gap:8px}
.dots i{width:10px;height:10px;border-radius:50%;background:#555}
.dots i:first-child{background:var(--purple)}

/* welcome */
.welcome{top:660px;height:338px;text-align:center}
.section-title{font-size:28px;font-weight:900;text-transform:uppercase;letter-spacing:.5px}
.welcome .section-title{margin-top:50px}
.welcome p{width:1020px;margin:18px auto 0;font-size:15px;line-height:24px;color:var(--text)}
.btn-solid{display:inline-flex;align-items:center;justify-content:center;background:var(--purple);color:var(--white);font-weight:900;font-size:14px;border-radius:24px;width:180px;height:46px;margin-top:38px}

/* services */
.services{top:998px;height:540px;background:var(--grey-bg)}
.services .section-title{position:absolute;top:55px;width:100%;text-align:center}
.service-card{top:115px;width:243px;height:364px;background:var(--white);text-align:center}
.service-card .photo{left:0;top:0;width:243px;height:171px}
.service-icon{position:absolute;left:87px;top:137px;width:68px;height:68px;border-radius:50%;background:var(--white);box-shadow:0 1px 4px rgba(0,0,0,.25);display:flex;align-items:center;justify-content:center}
.service-card h3{margin-top:222px;font-size:16px;font-weight:700;color:var(--purple);text-transform:uppercase;line-height:20px}
.service-card p{margin:10px 18px 0;font-size:14px;line-height:21px;color:var(--text)}

/* reviews */
.reviews{top:1538px;height:409px;background:linear-gradient(120deg,#3a3a3a,#1e1e1e 50%,#333)}
.reviews .section-title{position:absolute;top:48px;width:100%;text-align:center;color:var(--white)}
.review{top:132px;width:330px;text-align:center;color:var(--white)}
.review .quote{font-size:44px;font-weight:900;line-height:30px;height:34px}
.review p{font-style:italic;font-size:14px;line-height:25px;margin-top:8px}
.review .stars{color:var(--star);font-size:18px;letter-spacing:3px;margin-top:14px}
.review h4{font-size:14px;font-weight:900;margin-top:4px}

/* contact + blog */
.contact-blog{top:1947px;height:558px}
.quick-contact{left:74px;top:48px;width:330px;height:462px;background:var(--purple);padding:24px 22px}
.quick-contact h2{color:var(--white);font-size:29px;font-weight:900;margin-bottom:12px}
.field{background:var(--white);height:40px;margin-bottom:8px;font-size:13px;color:#555;padding:11px 10px}
.field.msg{height:100px}
.btn-submit{height:54px;margin-top:12px;background:linear-gradient(var(--orange-a),var(--orange-b));color:var(--white);font-weight:900;font-size:19px;display:flex;align-items:center;justify-content:center}
.blog-title{left:434px;top:52px;font-size:29px;font-weight:900}
.post{top:99px;width:332px}
.post .photo{position:relative;width:332px;height:201px}
.post h3{font-size:16px;font-weight:900;color:var(--purple);line-height:20px;margin-top:25px;text-transform:uppercase}
.post p{font-size:14px;line-height:22px;color:var(--text);margin-top:10px}
.post .more{font-size:14px;font-weight:900;margin-top:14px}

/* projects */
.projects{top:2505px;height:373px;background:var(--grey-bg)}
.projects .section-title{position:absolute;left:74px;top:40px}
.projects .arrows{position:absolute;right:74px;top:44px}
.project{top:93px;width:330px;height:218px}

/* footer */
.site-footer{top:2878px;height:297px;background:var(--footer);color:var(--footer-text)}
.f-brand{left:74px;top:70px;display:flex;align-items:center;gap:10px}
.f-brand .brand-mark{width:18px;height:18px;background:#8a8a8a}
.f-brand .brand-name{font-size:20px;font-weight:700;color:#bdbdbd}
.f-copy{left:74px;top:150px;font-size:12px;line-height:19px}
.social{left:74px;top:208px;display:flex;gap:16px}
.social i{width:18px;height:18px;border-radius:50%;background:var(--footer-text)}
.f-col{top:56px;font-size:13px}
.f-col h4{color:var(--white);font-size:15px;font-weight:900;margin-bottom:16px}
.f-col li{list-style:none;line-height:32px}
.f-col .two{display:grid;grid-template-columns:100px 100px}
.f-col .hl{color:var(--link-purple);font-weight:700}
.f-col .row{display:flex;gap:16px;align-items:center;line-height:32px}
</style>
</head>
<body>

<header class="site-header">
  <div class="abs brand"><span class="brand-mark"></span><span class="brand-name">K7 Electrical Services Ltd</span></div>
  <div class="abs top-contact">
    <span><svg width="14" height="14" viewBox="0 0 24 24"><path fill="#5c2a8a" d="M6.6 10.8a15 15 0 0 0 6.6 6.6l2.2-2.2c.3-.3.7-.4 1-.2 1.1.4 2.3.6 3.6.6.6 0 1 .4 1 1V20c0 .6-.4 1-1 1A17 17 0 0 1 3 4c0-.6.4-1 1-1h3.5c.6 0 1 .4 1 1 0 1.3.2 2.5.6 3.6.1.3 0 .7-.2 1z"/></svg>1-800-555-0142</span>
    <i class="sep"></i>
    <span><svg width="15" height="12" viewBox="0 0 24 18"><rect width="24" height="18" rx="2" fill="#5c2a8a"/><path d="M1 2l11 8 11-8" stroke="#fff" stroke-width="2" fill="none"/></svg>info@k7electrical.example</span>
  </div>
  <nav class="abs main-nav">
    <a class="active">Home</a><a>About Us</a><a>Services</a><a>Projects</a><a>Blog</a><a>Careers</a><a>Contact Us</a>
  </nav>
</header>

<section class="hero">
  <div class="photo" role="img" aria-label="Electrician in a hard hat working on a wired distribution panel"></div>
  <h1 class="abs hero-title">K7 ELECTRICAL<br>SERVICES</h1>
  <p class="abs hero-sub">We are a new electrical contracting company</p>
  <div class="abs btn-outline">CONTACT US</div>
  <div class="abs dots"><i></i><i></i><i></i><i></i></div>
</section>

<section class="welcome">
  <h2 class="section-title">Welcome to our website</h2>
  <p>Aliquam molestie, mi et imperdiet euismod, dui purus auctor tellus, et interdum lacus lectus et ante. Sed accumsan sollicitudin sapien, sit amet adipiscing turpis gravida ac. In congue, neque ac lobortis volutpat, libero mauris varius mi, vitae suscipit ipsum ligula vitae risus. Duis aliquam nibh a dui iaculis viverra id a velit. Vivamus egestas risus in magna varius commodo.<br>Sed semper viverra egestas. Etiam pretium porttitor lectus, vel ornare neque porta volutpat.</p>
  <div class="btn-solid">READ MORE</div>
</section>

<section class="services">
  <h2 class="section-title">Our Services</h2>
  <div class="abs service-card" style="left:74px">
    <div class="photo" role="img" aria-label="Electrician installing wiring" style="background:linear-gradient(135deg,#2f5c9a,#7aa0c8 60%,#e3a82b)"></div>
    <div class="service-icon"><svg width="26" height="26" viewBox="0 0 24 24"><circle cx="12" cy="12" r="7" fill="none" stroke="#5c2a8a" stroke-width="3" stroke-dasharray="3 2"/><circle cx="12" cy="12" r="3" fill="#5c2a8a"/></svg></div>
    <h3>Electrical<br>Installations</h3>
    <p>Vestibulum ante ipsum primis in faucibus orci luctus et ultrices posuere..</p>
  </div>
  <div class="abs service-card" style="left:345px">
    <div class="photo" role="img" aria-label="Tools laid on electrical plans" style="background:linear-gradient(135deg,#d8d8d8,#9a9a9a 55%,#c24a3a)"></div>
    <div class="service-icon"><svg width="26" height="26" viewBox="0 0 24 24"><path d="M4 20l9-9M14 4a5 5 0 0 0 6 6l-3-1-2-2z" stroke="#5c2a8a" stroke-width="3" fill="none" stroke-linecap="round"/></svg></div>
    <h3>Design &amp;<br>Maintenance</h3>
    <p>Vestibulum ante ipsum primis in faucibus orci luctus et ultrices posuere..</p>
  </div>
  <div class="abs service-card" style="left:614px">
    <div class="photo" role="img" aria-label="Electricians consulting at a workbench" style="background:linear-gradient(135deg,#c4c0ba,#8f8a85 60%,#5b6e88)"></div>
    <div class="service-icon"><svg width="26" height="26" viewBox="0 0 24 24"><path d="M12 3l9 8h-3v9h-4v-5h-4v5H6v-9H3z" fill="#5c2a8a"/></svg></div>
    <h3>Residential<br>Services</h3>
    <p>Vestibulum ante ipsum primis in faucibus orci luctus et ultrices posuere..</p>
  </div>
  <div class="abs service-card" style="left:882px">
    <div class="photo" role="img" aria-label="Electrician testing a commercial switchboard" style="background:linear-gradient(135deg,#e7d84a,#8a98a8 55%,#3d4856)"></div>
    <div class="service-icon"><svg width="26" height="26" viewBox="0 0 24 24"><rect x="6" y="2" width="12" height="20" fill="#5c2a8a"/><g fill="#fff"><rect x="8" y="5" width="3" height="3"/><rect x="13" y="5" width="3" height="3"/><rect x="8" y="10" width="3" height="3"/><rect x="13" y="10" width="3" height="3"/><rect x="8" y="15" width="3" height="3"/><rect x="13" y="15" width="3" height="3"/></g></svg></div>
    <h3>Commercial<br>Services</h3>
    <p>Vestibulum ante ipsum primis in faucibus orci luctus et ultrices posuere..</p>
  </div>
</section>

<section class="reviews" role="img" aria-label="Dark background of electrical tools and cables">
  <h2 class="section-title">Customer Reviews</h2>
  <div class="abs review" style="left:74px">
    <div class="quote">&#8220;</div>
    <p>Aliquam molestie, mi et imperdiet euismod, dui purus auctor tellus, et interdum lacus lectus et ante. Sed accumsan sollicitudin sapien, sit amet adipiscing turpis gravida ac..”</p>
    <div class="stars">★★★★★</div><h4>NAME HEADING</h4>
  </div>
  <div class="abs review" style="left:435px">
    <div class="quote">&#8220;</div>
    <p>Aliquam molestie, mi et imperdiet euismod, dui purus auctor tellus, et interdum lacus lectus et ante. Sed accumsan sollicitudin sapien, sit amet adipiscing turpis gravida ac..”</p>
    <div class="stars">★★★★★</div><h4>NAME HEADING</h4>
  </div>
  <div class="abs review" style="left:795px">
    <div class="quote">&#8220;</div>
    <p>Aliquam molestie, mi et imperdiet euismod, dui purus auctor tellus, et interdum lacus lectus et ante. Sed accumsan sollicitudin sapien, sit amet adipiscing turpis gravida ac..”</p>
    <div class="stars">★★★★★</div><h4>NAME HEADING</h4>
  </div>
</section>

<section class="contact-blog">
  <form class="abs quick-contact">
    <h2>QUICK CONTACT</h2>
    <div class="field">Name</div>
    <div class="field">Phone No</div>
    <div class="field">Email Address</div>
    <div class="field">Subject</div>
    <div class="field msg">Message</div>
    <div class="btn-submit">SUBMIT</div>
  </form>
  <h2 class="abs blog-title">BLOG POSTS</h2>
  <article class="abs post" style="left:434px">
    <div class="photo" role="img" aria-label="Electrician fitting a wall socket" style="background:linear-gradient(135deg,#e9e2da,#c9b9a6 50%,#4f79b5)"></div>
    <h3>Nam fermentum vestibulum purus id aliquet</h3>
    <p>Duis aliquam nibh a dui iaculis viverra id a velit. Vivamus egestas risus in magna varius commodo. Sed semper viverra egestas. Etiam pretium porttitor lectus,...</p>
    <div class="more">READ MORE</div>
  </article>
  <article class="abs post" style="left:794px">
    <div class="photo" role="img" aria-label="Electrician working on a ceiling fitting" style="background:linear-gradient(135deg,#f1c23a,#e8e4dc 45%,#2d4f9a)"></div>
    <h3>Nam fermentum vestibulum purus id aliquet</h3>
    <p>Duis aliquam nibh a dui iaculis viverra id a velit. Vivamus egestas risus in magna varius commodo. Sed semper viverra egestas. Etiam pretium porttitor lectus,...</p>
    <div class="more">READ MORE</div>
  </article>
</section>

<section class="projects">
  <h2 class="section-title">PROJECTS</h2>
  <svg class="arrows" width="40" height="20" viewBox="0 0 40 20"><path d="M10 3l-6 7 6 7M30 3l6 7-6 7" stroke="#1d1d1d" stroke-width="3" fill="none"/></svg>
  <div class="abs project" style="left:74px;background:linear-gradient(135deg,#d9d4cc,#e07a3a 55%,#7a7066)" role="img" aria-label="Electricians laying cable on a building site"></div>
  <div class="abs project" style="left:434px;background:linear-gradient(135deg,#f0c23a,#2f62b0 50%,#9aa6b2)" role="img" aria-label="Electrician working inside a control cabinet"></div>
  <div class="abs project" style="left:796px;background:linear-gradient(180deg,#c9c4bc,#7a7570 55%,#3a3f4e)" role="img" aria-label="Electrician installing pendant lighting"></div>
</section>

<footer class="site-footer">
  <div class="abs f-brand"><span class="brand-mark"></span><span class="brand-name">K7 Electrical Services Ltd</span></div>
  <p class="abs f-copy">Copyright © 2018. K7 Electrical Services Ltd<br>All Right Reserved</p>
  <div class="abs social"><i></i><i></i><i></i><i></i><i></i></div>
  <div class="abs f-col" style="left:384px">
    <h4>SITE MAP</h4>
    <ul class="two"><li>Home</li><li>Projects</li><li>About Us</li><li>Careers</li><li>Services</li><li>Contact Us</li><li>Blog</li></ul>
  </div>
  <div class="abs f-col" style="left:637px">
    <h4>RESOURCES</h4>
    <ul><li>Vestibulum ante</li><li>Ipsum primis</li><li>Faucibus orci luctus</li><li>Ultrices posuere</li><li>Cubilia</li></ul>
  </div>
  <div class="abs f-col" style="left:882px">
    <h4>CONTACT INFO</h4>
    <div class="hl">K7 ELECTRICAL</div>
    <div style="line-height:20px;margin-bottom:6px">4120 Larkfield<br>Road, Glasgow, G41 7QP</div>
    <div class="row"><svg width="12" height="12" viewBox="0 0 24 24"><path fill="#cfcfcf" d="M6.6 10.8a15 15 0 0 0 6.6 6.6l2.2-2.2c.3-.3.7-.4 1-.2 1.1.4 2.3.6 3.6.6.6 0 1 .4 1 1V20c0 .6-.4 1-1 1A17 17 0 0 1 3 4c0-.6.4-1 1-1h3.5c.6 0 1 .4 1 1 0 1.3.2 2.5.6 3.6.1.3 0 .7-.2 1z"/></svg>1-800-555-0142</div>
    <div class="row"><svg width="13" height="10" viewBox="0 0 24 18"><rect width="24" height="18" rx="2" fill="#cfcfcf"/><path d="M1 2l11 8 11-8" stroke="#2d2d2d" stroke-width="2" fill="none"/></svg>info@k7electrical.example</div>
    <div class="row"><svg width="12" height="14" viewBox="0 0 24 28"><path fill="#cfcfcf" d="M12 0a10 10 0 0 0-10 10c0 8 10 18 10 18s10-10 10-18A10 10 0 0 0 12 0zm0 14a4 4 0 1 1 0-8 4 4 0 0 1 0 8z"/></svg>Map Direction</div>
  </div>
</footer>

</body>
</html>
```